Jolly Paws Business Card Update

I have a business card which I love. I want to keep the same logo, colours, font and style. I want to upgrade the scripting and remove some elements and add others.
On the front side under Services - remove the existing wording and insert - Providing individual coaching strategies to create happy, healthy and social canine companions
Under Denise Carvell amend the current wording to read: Qualified in Dog Behavioural Training, Natural Animal Healthcare and Animal Health Science
On the reverse side to remove the web address.

```html
<!DOCTYPE html>
<html lang="en">
<head>
<meta charset="utf-8">
<title>Jolly Paws Business Card</title>
<link rel="stylesheet" href="https://fonts.googleapis.com/css2?family=Arimo:wght@400;700&display=swap">
<style>
  :root {
    --stage: #dcdcdc;
    --red-bright: #e8202a;
    --red-deep: #6e0a0f;
    --blue-light: #0a86cc;
    --blue-deep: #1f429c;
    --cream: #f3ecc8;
    --white: #ffffff;
    --text-font: "Arimo", Arial, sans-serif;
  }
  * { box-sizing: border-box; margin: 0; padding: 0; }
  html, body {
    width: 1200px;
    height: 800px;
    overflow: hidden;
    background: var(--stage);
    font-family: var(--text-font);
  }
  .canvas {
    position: relative;
    width: 1200px;
    height: 800px;
  }
  .card {
    position: absolute;
    top: 240px;
    width: 540px;
    height: 320px;
    border-radius: 22px;
    overflow: hidden;
    box-shadow: 0 12px 28px rgba(0,0,0,0.22);
  }
  /* Info side */
  .card--info {
    left: 40px;
    background: radial-gradient(circle at 62% 60%, var(--red-bright) 0%, #b3121a 40%, var(--red-deep) 100%);
  }
  .info-sweep {
    position: absolute;
    inset: 0;
  }
  .info-mark {
    position: absolute;
    left: 350px;
    top: 22px;
    width: 140px;
    text-align: center;
  }
  .mark-disc {
    display: block;
    width: 74px;
    height: 74px;
    margin: 0 auto 8px;
    border-radius: 50%;
    background: var(--cream);
  }
  .info-mark .mark-name {
    font-weight: 700;
    font-size: 17px;
    color: var(--cream);
  }
  .info-text {
    position: absolute;
    left: 36px;
    top: 62px;
    color: var(--white);
  }
  .heading {
    font-weight: 700;
    font-size: 17px;
    letter-spacing: 0.3px;
    text-transform: uppercase;
    margin-bottom: 3px;
  }
  .body-lines {
    font-size: 12.5px;
    line-height: 1.3;
    margin-bottom: 12px;
  }
  .contact-list { list-style: none; font-size: 12.5px; line-height: 1.45; }
  .contact-list li { display: flex; align-items: center; gap: 8px; }
  .contact-list svg { width: 11px; height: 11px; flex: none; }

  /* Brand side */
  .card--brand {
    left: 620px;
    background: linear-gradient(160deg, var(--blue-light) 0%, #1566b8 50%, var(--blue-deep) 100%);
    display: flex;
    flex-direction: column;
    align-items: center;
    justify-content: center;
  }
  .brand-disc {
    width: 120px;
    height: 120px;
    border-radius: 50%;
    background: var(--cream);
    margin-bottom: 18px;
  }
  .brand-name {
    font-weight: 700;
    font-size: 38px;
    color: var(--cream);
    text-transform: uppercase;
    letter-spacing: 1px;
  }
  .brand-tagline {
    margin-top: 4px;
    font-size: 17px;
    color: var(--white);
    letter-spacing: 0.6px;
    text-transform: uppercase;
  }
</style>
</head>
<body>
<main class="canvas">

  <section class="card card--info" aria-label="Card information side">
    <svg class="info-sweep" viewBox="0 0 540 320" aria-hidden="true">
      <polygon points="250,0 540,0 540,140 470,190" fill="#1567b8"/>
      <circle cx="410" cy="48" r="152" fill="#f3ecc8"/>
      <circle cx="420" cy="40" r="150" fill="#1a5cb0"/>
    </svg>

    <div class="info-mark">
      <span class="mark-disc"></span>
      <span class="mark-name">Jolly Paws</span>
    </div>

    <div class="info-text">
      <h2 class="heading">Services</h2>
      <p class="body-lines">Providing individual coaching<br>strategies to create happy,<br>healthy and social canine companions</p>

      <h2 class="heading">Denise Carvell</h2>
      <p class="body-lines">Qualified in Dog Behavioural Training,<br>Natural Animal Healthcare and<br>Animal Health Science</p>

      <ul class="contact-list">
        <li>
          <svg viewBox="0 0 12 12"><rect x="2.5" y="0.5" width="7" height="11" rx="1.2" fill="none" stroke="#fff" stroke-width="1.2"/></svg>
          0412 736 205
        </li>
        <li>
          <svg viewBox="0 0 12 12"><rect x="0.5" y="2" width="11" height="8" rx="1" fill="#fff"/><path d="M1 2.5 L6 6.5 L11 2.5" fill="none" stroke="#9a1016" stroke-width="1"/></svg>
          jollypaws1@mailbox.net
        </li>
      </ul>
    </div>
  </section>

  <section class="card card--brand" aria-label="Card brand side">
    <span class="brand-disc"></span>
    <h1 class="brand-name">Jolly Paws</h1>
    <p class="brand-tagline">Happy Dogs, Happy Owners</p>
  </section>

</main>
</body>
</html>
```